colour pencil case design

I am looking for a design for the front of a pencil case. The pencil case has 2 versions, 1 white fabric and 1 black fabric. The design should have 2 versions, eg. white word on black fabric and black words on white fabric. Its for children and teenagers’ aged 7 to 18. I can have 2 separate designs.
The pencil case is 22cm by 14cm. So the size of the image should be 18cm by 11cm. Files should be in png format and already in the correct size.
It must have the word “Believe”in big size. The letter b can be in capps or small letter. Prefer the font used in
I am looking for a background or image that can represent the phrase. If the design is good, I am open to also black and white theme.
Can also be black and white or colour... I have attached the font that I like for the main word "Believe". https://www.quillnest.net/gallery/583047192/Free-Font-Corvena-Modern-Script. Or you can use this font for the word Believe as well…. "Playlist script
Besides the word Believe, you should have the sentence ‘you can and you will”. It can be all in capps or small letter. (smaller size and different font from your word.
Target Market(s)
children and teenagers
Industry/Entity Type
tuition
Requirements
Must have
- The word Believe and the phrase I can and I will
Nice to have
- Some colourful pictures that can represent the phrase

```html
<!DOCTYPE html>
<html lang="en">
<head>
<meta charset="utf-8">
<title>Believe – Pencil Case Front, Dark and Light Versions</title>
<link rel="stylesheet" href="https://fonts.googleapis.com/css2?family=Dancing+Script:wght@600;700&family=Amatic+SC:wght@400;700&display=swap">
<style>
  :root {
    --ink: #000000;
    --paper: #ffffff;
    --page: #ffffff;
    --shadow: rgba(0, 0, 0, 0.55);
  }
  html, body {
    margin: 0;
    padding: 0;
    width: 1200px;
    height: 1000px;
    overflow: hidden;
    background: var(--page);
  }
  .canvas {
    position: relative;
    width: 1200px;
    height: 1000px;
    overflow: hidden;
  }
  .case-face {
    position: absolute;
    overflow: hidden;
    box-shadow: 8px 8px 10px var(--shadow);
  }
  .case-face--dark {
    left: 243px; top: 52px; width: 732px; height: 448px;
    background: var(--ink);
    color: var(--paper);
  }
  .case-face--light {
    left: 243px; top: 527px; width: 737px; height: 448px;
    background: var(--paper);
    color: var(--ink);
  }
  .splash-area {
    position: absolute;
    display: block;
  }
  .headline {
    position: absolute;
    margin: 0;
    font-family: "Dancing Script", cursive;
    font-weight: 700;
    line-height: 1;
    white-space: nowrap;
  }
  .tagline {
    position: absolute;
    margin: 0;
    font-family: "Amatic SC", sans-serif;
    white-space: nowrap;
    line-height: 1;
  }
  .case-face--dark .headline {
    left: 155px; top: 100px;
    font-size: 196px;
    letter-spacing: -5px;
  }
  .case-face--dark .tagline {
    left: 367px; top: 318px;
    font-size: 26px;
    font-weight: 400;
    letter-spacing: 4px;
    color: var(--paper);
  }
  .case-face--light .headline {
    left: 160px; top: 91px;
    font-size: 196px;
    letter-spacing: -5px;
  }
  .case-face--light .tagline {
    left: 302px; top: 330px;
    font-size: 41px;
    font-weight: 700;
    letter-spacing: 1px;
  }
  .brush-rule {
    position: absolute;
    left: 294px; top: 298px;
  }
</style>
</head>
<body>
<main class="canvas">

  <section class="case-face case-face--dark" aria-label="Black fabric version">
    <svg class="splash-area" style="left:-60px;top:-50px" width="260" height="290" viewBox="0 0 260 290" role="img" aria-label="White paint splash decoration, top left">
      <defs>
        <radialGradient id="splashWhiteA" cx="50%" cy="50%" r="50%">
          <stop offset="0" stop-color="#ffffff" stop-opacity="0.95"/>
          <stop offset="0.5" stop-color="#ffffff" stop-opacity="0.6"/>
          <stop offset="1" stop-color="#ffffff" stop-opacity="0"/>
        </radialGradient>
      </defs>
      <ellipse cx="130" cy="145" rx="130" ry="145" fill="url(#splashWhiteA)"/>
    </svg>
    <svg class="splash-area" style="left:480px;top:-40px" width="300" height="260" viewBox="0 0 300 260" role="img" aria-label="White paint splash decoration, top right">
      <defs>
        <radialGradient id="splashWhiteB" cx="50%" cy="50%" r="50%">
          <stop offset="0" stop-color="#ffffff" stop-opacity="0.95"/>
          <stop offset="0.5" stop-color="#ffffff" stop-opacity="0.6"/>
          <stop offset="1" stop-color="#ffffff" stop-opacity="0"/>
        </radialGradient>
      </defs>
      <ellipse cx="150" cy="130" rx="150" ry="130" fill="url(#splashWhiteB)"/>
    </svg>
    <svg class="splash-area" style="left:230px;top:360px" width="180" height="150" viewBox="0 0 180 150" role="img" aria-label="White paint splash decoration, bottom edge">
      <defs>
        <radialGradient id="splashWhiteC" cx="50%" cy="50%" r="50%">
          <stop offset="0" stop-color="#ffffff" stop-opacity="0.95"/>
          <stop offset="0.5" stop-color="#ffffff" stop-opacity="0.6"/>
          <stop offset="1" stop-color="#ffffff" stop-opacity="0"/>
        </radialGradient>
      </defs>
      <ellipse cx="90" cy="75" rx="90" ry="75" fill="url(#splashWhiteC)"/>
    </svg>

    <h1 class="headline">Believe</h1>
    <p class="tagline">YOU CAN AND YOU WILL</p>
  </section>

  <section class="case-face case-face--light" aria-label="White fabric version">
    <svg class="splash-area" style="left:-90px;top:0" width="260" height="400" viewBox="0 0 260 400" role="img" aria-label="Black ink splatter decoration, left edge">
      <defs>
        <radialGradient id="splashInkA" cx="50%" cy="50%" r="50%">
          <stop offset="0" stop-color="#000000" stop-opacity="0.95"/>
          <stop offset="0.5" stop-color="#000000" stop-opacity="0.6"/>
          <stop offset="1" stop-color="#000000" stop-opacity="0"/>
        </radialGradient>
      </defs>
      <ellipse cx="130" cy="200" rx="130" ry="200" fill="url(#splashInkA)"/>
    </svg>
    <svg class="splash-area" style="left:555px;top:-10px" width="180" height="200" viewBox="0 0 180 200" role="img" aria-label="Black ink splatter decoration, top right">
      <defs>
        <radialGradient id="splashInkB" cx="50%" cy="50%" r="50%">
          <stop offset="0" stop-color="#000000" stop-opacity="0.95"/>
          <stop offset="0.5" stop-color="#000000" stop-opacity="0.6"/>
          <stop offset="1" stop-color="#000000" stop-opacity="0"/>
        </radialGradient>
      </defs>
      <ellipse cx="90" cy="100" rx="90" ry="100" fill="url(#splashInkB)"/>
    </svg>

    <h2 class="headline">Believe</h2>
    <svg class="brush-rule" width="325" height="24" viewBox="0 0 325 24" role="img" aria-label="Dry brush stroke underline">
      <rect x="0" y="5" width="325" height="14" rx="4" fill="var(--ink)"/>
    </svg>
    <p class="tagline">YOU CAN AND YOU WILL</p>
  </section>

</main>
</body>
</html>
```